Hartwell Estates Business Cards

I would like a business card that includes myself and my partner.
Includes: Logo, office #, email, website, our names, our numbers and possibly the address. I would also like the logo to be embossed and the card to be horizontal.
There is a photo of our yard signs to give you an idea of the colors of our business.

Target Market(s)

Everyone in real estate market.
We are in a rural area. Our clientele are from all socioeconomic backgrounds.

Industry/Entity Type

Real Estate Agent

Contact Information for Business Card

Company Name: Hartwell Estates
Our Names, Titles & Cell #'s : Dana Pembrook-Broker (555).317.6624, Marla Pembrook-Realtor (555).609.1385
Office #: (555).240.3918
Website: hartwellestates-demo.com
Joint Email: pembrook@hartwellestates-demo.com
Office Address: 418B W. Calloway Ave.
Cedar Bend, OK. 70913

Font styles to use
Serif

Requirements
Must have
• HORIZONTAL, Logo, Myself and my partners names, Our cell #'s, our office #, our website, our email address
Nice to have
• Embossed logo, office address, our titles.

```html
<!DOCTYPE html>
<html lang="en">
<head>
<meta charset="utf-8">
<title>Hartwell Estates Business Cards</title>
<link rel="stylesheet" href="https://fonts.googleapis.com/css2?family=Crimson+Text:wght@700&family=Source+Sans+3:wght@400;600&display=swap">
<style>
  :root {
    --purple: #4a2266;
    --white: #ffffff;
    --backdrop: #ecebee;
    --ink-light: #ffffff;
  }
  * { margin: 0; padding: 0; box-sizing: border-box; }
  html, body {
    width: 1200px; height: 900px; overflow: hidden;
    background: var(--backdrop);
  }
  .canvas { position: relative; width: 1200px; height: 900px; }

  .card {
    position: absolute;
    background: var(--white);
    overflow: hidden;
    box-shadow: 0 4px 14px rgba(0,0,0,0.18);
  }

  /* Front card */
  .card-front { left: 77px; top: 34px; width: 589px; height: 364px; }
  .front-brand {
    position: absolute; left: 0; top: 0; width: 100%; height: 174px;
    display: flex; flex-direction: column; align-items: center; justify-content: center;
    font-family: "Crimson Text", Georgia, serif; font-weight: 700; color: var(--purple);
    line-height: 1;
  }
  .front-brand .brand-main { font-size: 56px; letter-spacing: 1px; }
  .front-brand .brand-sub { font-size: 38px; margin-top: 12px; }

  .contact-band {
    position: absolute; left: 0; top: 174px; width: 100%; height: 190px;
    background: var(--purple); color: var(--ink-light);
    font-family: "Source Sans 3", Arial, sans-serif;
  }
  .agent { position: absolute; left: 30px; }
  .agent-broker { top: 16px; }
  .agent-realtor { top: 98px; }
  .agent-name { font-size: 21px; font-weight: 600; line-height: 24px; }
  .agent-title { font-size: 15px; line-height: 18px; }
  .agent-phone { font-size: 16px; line-height: 22px; margin-top: 4px; display: flex; align-items: center; gap: 6px; }

  .office { position: absolute; right: 37px; text-align: right; font-size: 16px; line-height: 21px; }
  .office-address { top: 29px; }
  .office-lines { top: 100px; }
  .office-lines .line { display: flex; justify-content: flex-end; align-items: center; gap: 6px; }
  .icon { width: 12px; height: 12px; flex: none; }

  /* Back card */
  .card-back { left: 388px; top: 505px; width: 567px; height: 352px; }
  .side-block { position: absolute; top: 110px; height: 131px; width: 102px; background: var(--purple); }
  .side-block.left { left: 0; }
  .side-block.right { right: 0; }
  .back-brand {
    position: absolute; left: 102px; right: 102px; top: 110px; height: 131px;
    display: flex; align-items: center; justify-content: center; gap: 16px;
    font-family: "Crimson Text", Georgia, serif; font-weight: 700; color: var(--purple);
  }
  .brand-square { width: 58px; height: 58px; background: var(--purple); flex: none; }
  .back-brand .brand-text { display: flex; flex-direction: column; align-items: center; line-height: 1; }
  .back-brand .brand-main { font-size: 44px; letter-spacing: 1px; }
  .back-brand .brand-sub { font-size: 30px; margin-top: 8px; }
</style>
</head>
<body>
<main class="canvas">

  <section class="card card-front" aria-label="Business card front">
    <div class="front-brand">
      <span class="brand-main">HARTWELL</span>
      <span class="brand-sub">Estates</span>
    </div>

    <div class="contact-band">
      <div class="agent agent-broker">
        <div class="agent-name">Dana Pembrook</div>
        <div class="agent-title">Broker</div>
        <div class="agent-phone">
          <svg class="icon" viewBox="0 0 12 12" aria-hidden="true"><path fill="#fff" d="M2.5 1 4.3 3 3.3 4.3c.7 1.6 2.3 3.2 4.2 4.3L8.8 7.6 11 9.4 9.8 11C5.2 10.6 1.2 6.6 1 2.2Z"/></svg>
          (555).317.6624
        </div>
      </div>
      <div class="agent agent-realtor">
        <div class="agent-name">Marla Pembrook</div>
        <div class="agent-title">Realtor</div>
        <div class="agent-phone">
          <svg class="icon" viewBox="0 0 12 12" aria-hidden="true"><path fill="#fff" d="M2.5 1 4.3 3 3.3 4.3c.7 1.6 2.3 3.2 4.2 4.3L8.8 7.6 11 9.4 9.8 11C5.2 10.6 1.2 6.6 1 2.2Z"/></svg>
          (555).609.1385
        </div>
      </div>

      <div class="office office-address">
        <div>418B W. Calloway Ave.</div>
        <div>Cedar Bend, OK. 70913</div>
      </div>

      <div class="office office-lines">
        <div class="line">(555).240.3918
          <svg class="icon" viewBox="0 0 12 12" aria-hidden="true"><path fill="#fff" d="M2.5 1 4.3 3 3.3 4.3c.7 1.6 2.3 3.2 4.2 4.3L8.8 7.6 11 9.4 9.8 11C5.2 10.6 1.2 6.6 1 2.2Z"/></svg>
        </div>
        <div class="line">pembrook@hartwellestates-demo.com
          <svg class="icon" viewBox="0 0 12 12" aria-hidden="true"><rect x="1" y="2.5" width="10" height="7" fill="#fff"/><path d="M1 2.5 6 6.5 11 2.5" fill="none" stroke="#4a2266" stroke-width="1"/></svg>
        </div>
        <div class="line">hartwellestates-demo.com
          <svg class="icon" viewBox="0 0 12 12" aria-hidden="true"><circle cx="6" cy="6" r="5" fill="#fff"/><path d="M1 6h10M6 1c-2 2.5-2 7.5 0 10M6 1c2 2.5 2 7.5 0 10" fill="none" stroke="#4a2266" stroke-width="0.8"/></svg>
        </div>
      </div>
    </div>
  </section>

  <section class="card card-back" aria-label="Business card back">
    <div class="side-block left"></div>
    <div class="side-block right"></div>
    <div class="back-brand">
      <span class="brand-square" aria-hidden="true"></span>
      <span class="brand-text">
        <span class="brand-main">HARTWELL</span>
        <span class="brand-sub">Estates</span>
      </span>
    </div>
  </section>

</main>
</body>
</html>
```